Creative, fresh business card design for Ripplecraft Facades

We need a fresh, creative business card design for Ripplecraft Facades. We are the manufacturer of Ripplecraft Facades in Australia. Wall panels are 2400 x 1200mm panels made from MDF and feature 3D patterns on the face of the panel. The colours to be used are green, silver/grey and white RGB
Red 187
Green 207
Blue 65.

An idea is to possibly use a watermark of one of our designs as a background (like on the "Grids" design on the left hand side of page 2 of our brochure).

Target Market(s)

Interior designers, architects, builders and home renovators

Industry/Entity Type

Business

Contact Information for Business Card

Details to go on the card are:
Our logo (attached),
Slogan: "Decorative panels for interiors and exteriors",
Contact name,
Position,
Mobile phone number,
Business address,
Business phone,
Business fax,
Website and
Email address.

I have attached a few images of our panels and our brochure for reference.

The colours of the business card should feature our logo colours which are: RGB
Red 187
Green 207
Blue 65

Requirements
Must have
• Very modern fonts and design. Some of the designs shown especially the "Prisms" design which is a popular design.
Nice to have
• Creative but simple design. Very contemporary.
Should not have
• Anything ornate or old fashioned.

```html
<!DOCTYPE html>
<html lang="en">
<head>
<meta charset="utf-8">
<title>Ripplecraft Facades – Business Card</title>
<link href="https://fonts.googleapis.com/css2?family=Arimo:wght@400;700&display=swap" rel="stylesheet">
<style>
  :root {
    --lime: #bbcf41;
    --grey: #8a8a8a;
    --ink: #4a4a4a;
    --rule: #9aa3a8;
    --paper: #ffffff;
    --backdrop: #e9e7e3;
    --photo-a: #b8304a;
    --photo-b: #d95a6a;
    --photo-c: #c9a24a;
  }
  * { margin: 0; padding: 0; box-sizing: border-box; }
  html, body { width: 1200px; height: 987px; overflow: hidden; }
  body {
    background: var(--backdrop);
    font-family: "Arimo", Arial, sans-serif;
    position: relative;
  }
  .card {
    position: absolute;
    left: 293px;
    width: 615px;
    height: 349px;
    box-shadow: 0 2px 6px rgba(0,0,0,.25);
    overflow: hidden;
  }
  .card--front { top: 131px; background: var(--paper); }
  .card--back { top: 506px; }

  .brand {
    position: absolute;
    top: 52px; left: 0; right: 0;
    display: flex; justify-content: center; align-items: center; gap: 12px;
  }
  .brand__square { width: 30px; height: 30px; background: var(--lime); }
  .brand__name { font-size: 38px; font-weight: 700; color: var(--lime); letter-spacing: -0.5px; }
  .tagline {
    position: absolute;
    top: 160px; left: 0; right: 0;
    text-align: center;
    font-size: 13px; line-height: 16px;
    letter-spacing: 2.4px;
    color: var(--grey);
  }
  .person {
    position: absolute;
    top: 212px; left: 0; right: 0;
    text-align: center;
    font-size: 17px; color: var(--grey);
  }
  .person__name { color: var(--lime); font-weight: 700; font-size: 22px; }
  .divider {
    position: absolute;
    top: 241px; left: 30px; right: 30px;
    height: 1px; background: var(--rule);
  }
  .contacts {
    position: absolute;
    top: 255px; left: 30px;
    list-style: none;
    font-size: 16px; line-height: 24px; color: var(--ink);
  }
  .contacts li { display: flex; align-items: center; gap: 9px; }
  .contacts svg { width: 14px; height: 14px; fill: var(--lime); }
  .address {
    position: absolute;
    top: 255px; right: 32px;
    text-align: right;
    font-size: 16px; line-height: 22px; color: var(--ink);
    font-style: normal;
  }
  .address__web { letter-spacing: 1px; }

  .photo {
    position: absolute; inset: 0;
    background:
      linear-gradient(90deg, rgba(0,0,0,0) 55%, rgba(230,200,140,.55) 75%, rgba(200,170,120,.5) 100%),
      linear-gradient(135deg, var(--photo-b) 0%, var(--photo-a) 45%, #8e2238 100%);
  }
  .brand--back {
    position: absolute;
    top: 185px; left: 41px;
    display: flex; align-items: center; gap: 10px;
  }
  .brand--back .brand__name { color: var(--paper); font-size: 27px; }
  .brand--back .brand__square { background: var(--paper); width: 22px; height: 22px; }
  .tagline--back {
    position: absolute;
    top: 305px; left: 41px;
    font-size: 12px; line-height: 15px;
    letter-spacing: 2.2px; color: var(--paper);
  }
</style>
</head>
<body>
  <section class="card card--front">
    <div class="brand">
      <span class="brand__square"></span>
      <span class="brand__name">Ripplecraft Facades</span>
    </div>
    <p class="tagline">decorative panels for<br>interiors &amp; landscapes</p>
    <p class="person"><span class="person__name">DANIEL HARROW -</span> CEO&amp;Founder</p>
    <div class="divider"></div>
    <ul class="contacts">
      <li><svg viewBox="0 0 24 24"><path d="M6.6 10.8a15 15 0 0 0 6.6 6.6l2.2-2.2a1 1 0 0 1 1-.25 11.4 11.4 0 0 0 3.6.57 1 1 0 0 1 1 1V20a1 1 0 0 1-1 1A17 17 0 0 1 3 4a1 1 0 0 1 1-1h3.5a1 1 0 0 1 1 1c0 1.25.2 2.45.57 3.57a1 1 0 0 1-.25 1z"/></svg>(555) 201-4478</li>
      <li><svg viewBox="0 0 24 24"><path d="M6 2h12v5H6zM3 8h18v9h-3v5H6v-5H3zm5 7v5h8v-5z"/></svg>(555) 201-4479</li>
      <li><svg viewBox="0 0 24 24"><path d="M2 5h20v14H2zm2 2v.5l8 5 8-5V7z"/></svg>dharrow@ripplecraftfacades.com</li>
    </ul>
    <address class="address">
      42 Larkspur Way<br>
      Millbrook, Westvale 20917<br>
      <span class="address__web">www.ripplecraftfacades.com</span>
    </address>
  </section>

  <section class="card card--back">
    <div class="photo" role="img" aria-label="Interior photo of a red faceted 3D wall panel with pendant lamps and glass shelves holding coloured vases"></div>
    <div class="brand brand--back">
      <span class="brand__square"></span>
      <span class="brand__name">Ripplecraft Facades</span>
    </div>
    <p class="tagline--back">decorative panels for<br>interiors &amp; landscapes</p>
  </section>
</body>
</html>
```